New web page, 2 companies on the one page

A new web page for an engineering consultancy and maintenance management company

Corlett & Associates is the parent company covering the design and consultancy
Valtrix Engineering is the Maintenance and Reliability company

Target Market(s)

Food & Beverage, ingredients Manufacturing
engineering managers

Coding

Coded - Design and coding required

Number of Pages Required

1 page

Font styles to use
Other font styles liked:
• Roboto

Colors
1861ab
85acd3
d0dfed
cee9f5

```html
<!DOCTYPE html>
<html lang="en">
<head>
<meta charset="utf-8">
<title>Corlett &amp; Associates</title>
<link href="https://fonts.googleapis.com/css2?family=Montserrat:wght@400;500;600;700&family=Open+Sans:wght@400;600;700&family=PT+Serif&family=Roboto:wght@300;400&display=swap" rel="stylesheet">
<style>
:root{
  --blue:#1aa3dd;
  --blue-deep:#1861ab;
  --blue-soft:#85acd3;
  --ink:#1b1b1b;
  --text:#555;
  --muted:#8a8a8a;
  --dark:#101216;
  --white:#fff;
  --grey-frame:#8a8b8d;
}
*{margin:0;padding:0;box-sizing:border-box}
html,body{width:1200px;height:3727px;overflow:hidden;background:var(--white)}
body{position:relative;font-family:'Open Sans',sans-serif;color:var(--ink)}
.abs{position:absolute}
.heading{font-family:'Montserrat',sans-serif;font-weight:600;letter-spacing:-.5px}
.accent{color:var(--blue)}

/* header */
.site-header{left:0;top:0;width:1200px;height:85px;background:#000}
.brand{left:123px;top:22px;display:flex;align-items:center;gap:12px;color:var(--white);font-family:'Montserrat',sans-serif;font-weight:700;font-size:20px}
.brand-mark{width:40px;height:40px;background:var(--blue);flex:none}
.main-nav{right:111px;top:32px;display:flex;gap:23px;font-family:'Montserrat',sans-serif;font-size:15px;color:var(--white)}
.main-nav .active{color:var(--blue)}

/* hero */
.hero-photo{left:0;top:85px;width:1200px;height:680px;background:linear-gradient(180deg,#4d5a6a 0%,#8a7f6c 40%,#c68a45 62%,#3f3a36 78%,#2a2826 100%)}
.hero-title{left:108px;top:366px;font-size:52px;color:var(--white)}
.hero-text{left:110px;top:432px;width:560px;font-size:17px;line-height:36px;color:var(--white)}
.btn{left:111px;top:508px;width:155px;height:52px;background:var(--blue);color:var(--white);font-family:'Montserrat',sans-serif;font-weight:600;font-size:16px;display:flex;align-items:center;justify-content:center}
.slider-arrow{color:var(--white);font-size:44px;font-family:'Montserrat',sans-serif}

/* about */
.about-photo{left:111px;top:952px;width:448px;height:488px;background:linear-gradient(160deg,#6b87a6,#c9d5e2 45%,#4e5a68)}
.about-kicker{left:599px;top:990px;font-family:'PT Serif',serif;font-size:25px;color:var(--blue)}
.about-title{left:599px;top:1038px;font-size:27px}
.about-list{left:599px;top:1104px;width:480px;list-style:none;font-family:'Roboto',sans-serif;font-weight:300;font-size:14px;line-height:31px;color:var(--text)}
.about-list li{position:relative;padding-left:21px;margin-bottom:22px}
.about-list li::before{content:"\00BB";position:absolute;left:0;top:-4px;font-size:22px;color:var(--blue)}

/* services */
.section-title{width:1200px;left:0;text-align:center;font-size:42px}
.service-photo{top:1872px;width:304px;height:295px}
.service-label{top:2177px;width:304px;text-align:center;color:var(--white);font-weight:600;font-size:16px;line-height:26px}

/* news */
.news-card{top:2617px;width:317px;height:452px;background:var(--white);box-shadow:0 2px 10px rgba(0,0,0,.15)}
.news-photo{width:317px;height:229px}
.news-body{padding:22px 10px 0;font-family:'Montserrat',sans-serif}
.news-lead{font-size:14px;font-weight:500;line-height:29px;color:#2b2b2b}
.news-sub{margin-top:10px;font-size:14px;color:var(--muted)}
.news-foot{position:absolute;left:0;bottom:0;width:100%;height:56px;border-top:1px solid #e4e4e4;display:flex;align-items:center;justify-content:space-between;padding:0 17px;font-family:'Montserrat',sans-serif;font-size:14px;color:#333}
.dots{display:flex;gap:4px}
.dots i{width:6px;height:6px;border-radius:50%;background:#333}
.dots i:nth-child(2){background:#aaa}

/* footer */
.footer-bg{left:0;top:3174px;width:1200px;height:553px;background:linear-gradient(180deg,#2a2e36,#15181d 60%,#0e1013)}
.footer-brand{left:111px;top:3455px;display:flex;align-items:center;gap:12px;color:var(--white);font-family:'Montserrat',sans-serif;font-weight:700;font-size:21px}
.footer-brand .brand-mark{width:46px;height:46px}
.footer-head{font-family:'Montserrat',sans-serif;font-weight:600;font-size:15px;color:var(--white);letter-spacing:-.3px}
.footer-links{list-style:none;font-family:'Montserrat',sans-serif;font-size:16px;color:var(--white);line-height:34px}
.contact-row{display:flex;gap:14px;align-items:flex-start;font-family:'Montserrat',sans-serif;font-size:16px;color:var(--white);line-height:28px}
.social li{display:flex;align-items:center;gap:10px;height:39px}
.social i{width:31px;height:31px;border:2px solid var(--white);border-radius:50%}
.footer-rule{left:111px;top:3629px;width:977px;height:1px;background:#888}
.copyright{left:0;top:3666px;width:1200px;text-align:center;font-family:'Montserrat',sans-serif;font-size:15px;color:var(--white)}
</style>
</head>
<body>

<header class="site-header abs">
  <div class="brand abs"><span class="brand-mark"></span>Corlett &amp; Associates</div>
  <nav class="main-nav abs">
    <span class="active">HOME</span><span>ABOUT</span><span>SERVICES</span><span>BLOG</span><span>REVIEWS</span><span>CONTACT</span>
  </nav>
</header>

<section class="hero">
  <div class="hero-photo abs" role="img" aria-label="Engineers on a construction site at sunset with a tower crane"></div>
  <svg class="abs" style="left:0;top:700px" width="1200" height="160" viewBox="0 700 1200 160">
    <polygon points="0,720 599,790 1200,720 1200,860 0,860" fill="var(--white)"/>
    <polygon points="0,720 596,810 596,847 0,760" fill="var(--blue)"/>
    <polygon points="1200,720 603,810 603,847 1200,760" fill="var(--blue)"/>
  </svg>
  <div class="slider-arrow abs" style="left:72px;top:372px">&#10094;</div>
  <div class="slider-arrow abs" style="left:1100px;top:372px">&#10095;</div>
  <h1 class="hero-title heading abs">CORLETT &amp; ASSOCIATES</h1>
  <p class="hero-text abs">Corlett &amp; Associates is specialised manufacturing engineering support organisation that can provide fast, nimble, and flexible services.</p>
  <a class="btn abs">GET STARTED</a>
</section>

<section class="about">
  <svg class="abs" style="left:0;top:1240px" width="350" height="252">
    <path d="M0 2H347V248H0" fill="none" stroke="#5b8aa6" stroke-width="1.2"/>
  </svg>
  <div class="about-photo abs" role="img" aria-label="Business team meeting in a glass-walled office"></div>
  <div class="about-kicker abs">About Us</div>
  <h2 class="about-title heading abs">WELCOME TO <span class="accent">CORLETT &amp; ASSOCIATES</span></h2>
  <ul class="about-list abs">
    <li>Corlett &amp; Associates is specialised manufacturing engineering support organisation that can provide fast, nimble, and flexible services.</li>
    <li>We have a proven track record in delivering tangible outcomes in process design and fit-out, projectmanagement, manufacturing process and maintenance design and execution.</li>
    <li>Our specialist focus in food manufacturing across a range of sectors allows our team to deliver real benefits to performance and recognition of the clients investment</li>
  </ul>
</section>

<section class="services">
  <svg class="abs" style="left:0;top:1549px" width="1200" height="880" viewBox="0 1549 1200 880">
    <polygon points="0,1549 1200,1549 1200,2316 599,2427 0,2316" fill="#1a1c20"/>
    <polygon points="84,1640 596,1735 596,1750 98,1657 98,2250 596,2343 596,2358 84,2262" fill="var(--grey-frame)"/>
    <polygon points="1117,1640 603,1735 603,1750 1103,1657 1103,2250 603,2343 603,2358 1117,2262" fill="var(--blue)"/>
    <rect x="597" y="1549" width="5" height="880" fill="#000"/>
  </svg>
  <h2 class="section-title heading abs" style="top:1780px;color:var(--white)">OUR <span class="accent">SERVICES</span></h2>
  <div class="slider-arrow abs" style="left:70px;top:1960px">&#10094;</div>
  <div class="slider-arrow abs" style="left:1102px;top:1960px">&#10095;</div>
  <div class="service-photo abs" style="left:129px;background:linear-gradient(150deg,#2c5f8e,#8ab0c8 50%,#c8c23a)" role="img" aria-label="Engineer working at a CAD workstation"></div>
  <div class="service-photo abs" style="left:447px;background:linear-gradient(160deg,#8d5d4a,#d9d6d1 45%,#6b6a66)" role="img" aria-label="Team planning a project at a whiteboard"></div>
  <div class="service-photo abs" style="left:764px;background:linear-gradient(160deg,#5a4a40,#a08c78 40%,#e07a28 75%,#c9d640)" role="img" aria-label="Site engineers in hard hats inspecting a building"></div>
  <div class="service-label abs" style="left:129px">PROCESS FACILITIES DESIGN</div>
  <div class="service-label abs" style="left:447px">PROJECT MANAGEMENT</div>
  <div class="service-label abs" style="left:764px">ENGINEERING MAINTENANCE<br>MANAGEMENT</div>
</section>

<section class="news">
  <h2 class="section-title heading abs" style="top:2522px">LATEST <span class="accent">NEWS</span></h2>
  <svg class="abs" style="left:76px;top:2833px" width="1050" height="20">
    <path d="M12 2 4 10 12 18M1032 2 1040 10 1032 18" fill="none" stroke="#222" stroke-width="2"/>
  </svg>
  <article class="news-card abs" style="left:111px">
    <div class="news-photo" style="background:linear-gradient(160deg,#c77d3a,#e7d55a 55%,#5b6a3a)" role="img" aria-label="Surveyors in safety vests on site"></div>
    <div class="news-body"><p class="news-lead">Lorem ipsum dolor sit amet, consectetur adipiscing elit, sed do eiusmod tempor incididunt ut labore et dolore</p><p class="news-sub">Sed ut perspiciatis unde omnis iste</p></div>
    <div class="news-foot"><span>March 20,2021</span><span class="dots"><i></i><i></i><i></i></span></div>
  </article>
  <article class="news-card abs" style="left:441px">
    <div class="news-photo" style="background:linear-gradient(160deg,#8a8f96,#d8c66a 50%,#4d5560)" role="img" aria-label="Engineering team discussing plans"></div>
    <div class="news-body"><p class="news-lead">Lorem ipsum dolor sit amet, consectetur adipiscing elit, sed do eiusmod tempor incididunt ut labore et dolore</p><p class="news-sub">Sed ut perspiciatis unde omnis iste</p></div>
    <div class="news-foot"><span>March 20,2021</span><span class="dots"><i></i><i></i><i></i></span></div>
  </article>
  <article class="news-card abs" style="left:771px">
    <div class="news-photo" style="background:linear-gradient(160deg,#e8e4de,#b9b3ab 55%,#3a3a3a)" role="img" aria-label="Tablet showing a building design on a desk"></div>
    <div class="news-body"><p class="news-lead">Lorem ipsum dolor sit amet, consectetur adipiscing elit, sed do eiusmod tempor incididunt ut labore et dolore</p><p class="news-sub">Sed ut perspiciatis unde omnis iste</p></div>
    <div class="news-foot"><span>March 20,2021</span><span class="dots"><i></i><i></i><i></i></span></div>
  </article>
</section>

<footer class="site-footer">
  <div class="footer-bg abs" role="img" aria-label="Industrial plant with storage tanks at dusk"></div>
  <svg class="abs" style="left:0;top:3170px" width="1200" height="110" viewBox="0 3170 1200 110">
    <polygon points="0,3170 596,3170 596,3210 0,3270" fill="var(--white)"/>
    <polygon points="1200,3170 603,3170 603,3210 1200,3270" fill="var(--white)"/>
    <polygon points="0,3270 596,3210 596,3175 0,3235" fill="var(--blue)"/>
    <polygon points="1200,3270 603,3210 603,3175 1200,3235" fill="var(--blue)"/>
  </svg>
  <div class="footer-brand abs"><span class="brand-mark"></span>Valtrix Engineering</div>

  <div class="abs" style="left:443px;top:3358px">
    <div class="footer-head">QUICKLINKS</div>
    <ul class="footer-links" style="margin-top:16px">
      <li>Home</li><li>About</li><li>Services</li><li>Blog</li><li>Reviews</li><li>Contact</li>
    </ul>
  </div>

  <div class="abs" style="left:627px;top:3358px">
    <div class="footer-head">CONTACT US</div>
    <div class="contact-row" style="margin-top:24px">
      <svg width="16" height="16" viewBox="0 0 24 24"><path d="M6 2 10 6 8 9c1.5 3 4 5.5 7 7l3-2 4 4-3 4C10 21 3 14 2 5Z" fill="none" stroke="#fff" stroke-width="1.6"/></svg>
      <span style="margin-left:8px">888-888-8888</span>
    </div>
    <div class="contact-row" style="margin-top:14px">
      <svg width="14" height="20" viewBox="0 0 14 20"><path d="M7 0a7 7 0 0 0-7 7c0 5 7 13 7 13s7-8 7-13a7 7 0 0 0-7-7Zm0 10a3 3 0 1 1 0-6 3 3 0 0 1 0 6Z" fill="#fff"/></svg>
      <span>Lorem ipsum dolor sit amet,<br>consectetur adipiscing</span>
    </div>
    <div class="contact-row" style="margin-top:12px">
      <svg width="16" height="14" viewBox="0 0 16 12"><rect x=".7" y=".7" width="14.6" height="10.6" fill="none" stroke="#fff" stroke-width="1.2"/><path d="M1 1l7 6 7-6" fill="none" stroke="#fff" stroke-width="1.2"/></svg>
      <span>info@corlettassociates.com</span>
    </div>
  </div>

  <div class="abs" style="left:944px;top:3358px">
    <div class="footer-head">CONNECT WITH US</div>
    <ul class="social footer-links" style="margin-top:14px">
      <li><i></i>Nestly</li><li><i></i>Glimmer</li><li><i></i>Chatterly</li><li><i></i>Workline</li>
    </ul>
  </div>

  <div class="footer-rule abs"></div>
  <p class="copyright abs">copyrights © 2021 All Rights Reserved</p>
</footer>

</body>
</html>
```